KVOR Individual and Corporate Development Business Card Design

KVOR needs a business card design that is aligned with it's values and targetted markets. Coherent Lattice of Adaptive Reasoning Method's self diagnosis model and tools, which can be used for personal improvement and team/business performance enhancement, is based on the learnings of over 20 years of medical practitioning. KVOR supercharges personal effectiveness and awareness to also increase team and business performance.

The targetted markets are high performance individuals and teams who aspire seek to enhance their capabilities and achieve their absolute best potential.

Look and feel for the business card design we are looking for is high technology, premium, fresh, new and medical.

Target Market(s)

Industry/Entity Type

Business Consultant

Contact Information for Business Card

Logo, Full Name, Title, Phone number, Email, company name, Address,

Font styles to use
Sans Serif

Requirements
Must have
• Tag line: Sharpening Clarity for Driven Teams and Their Leaders
• Please use same colours as the logo.

```html
<!DOCTYPE html>
<html lang="en">
<head>
<meta charset="utf-8">
<title>KVOR Business Card</title>
<link href="https://fonts.googleapis.com/css2?family=Roboto:ital,wght@0,400;0,500;0,700;1,400&family=Roboto+Condensed:wght@700&display=swap" rel="stylesheet">
<style>
  :root {
    --backdrop: #2b2c2e;
    --card-light: #f2f2f2;
    --card-dark: #5b5e63;
    --teal: #03a9c1;
    --slate: #5b5e63;
    --white: #ffffff;
  }
  * { margin: 0; padding: 0; box-sizing: border-box; }
  html, body {
    width: 1200px; height: 960px; overflow: hidden;
    background: var(--backdrop);
    font-family: "Roboto", Arial, sans-serif;
  }
  .canvas { position: relative; width: 1200px; height: 960px; }
  .card {
    position: absolute; width: 600px; height: 343px; overflow: hidden;
  }
  .card-front { left: 314px; top: 113px; background: var(--card-light); }
  .card-back { left: 311px; top: 472px; background: var(--card-dark); }

  .brand {
    position: absolute; left: 0; right: 0; text-align: center;
    font-family: "Roboto", Arial, sans-serif; font-weight: 700;
  }
  .brand-name { font-size: 58px; letter-spacing: 4px; line-height: 1; }
  .brand-full {
    margin-top: 14px; font-size: 15px; letter-spacing: 0.6px; line-height: 1.1;
    text-transform: uppercase;
  }
  .card-front .brand { top: 64px; color: var(--teal); }
  .card-back .brand { top: 134px; color: var(--white); }
  .brand-mark {
    display: inline-block; width: 12px; height: 12px; border-radius: 50%;
    background: currentColor; margin-left: 8px; vertical-align: 34px;
  }

  .contact-band { position: absolute; left: 0; top: 0; width: 600px; height: 343px; }

  .person {
    position: absolute; left: 21px; top: 229px; color: var(--white);
  }
  .person-name {
    font-family: "Roboto Condensed", "Arial Narrow", sans-serif;
    font-size: 20px; font-weight: 700; line-height: 1;
  }
  .person-title { font-size: 14.5px; font-weight: 500; margin-top: 4px; }
  .contact-list { list-style: none; margin-top: 10px; font-size: 14.5px; line-height: 20px; }
  .contact-list li { display: flex; align-items: center; gap: 7px; }
  .contact-list svg { width: 14px; height: 14px; fill: var(--white); }

  .company {
    position: absolute; right: 26px; top: 238px; text-align: right;
    color: var(--white); font-size: 14.5px; line-height: 18px;
  }
  .company-name { font-weight: 500; }
  .company-address { margin-top: 8px; }

  .tagline {
    position: absolute; left: 0; right: 0; top: 292px; text-align: center;
    color: var(--white); font-style: italic; font-size: 14.5px;
  }
</style>
</head>
<body>
<main class="canvas">

  <section class="card card-front" aria-label="Business card front">
    <div class="brand">
      <div class="brand-name">KVOR<span class="brand-mark"></span></div>
      <div class="brand-full">Coherent Lattice of<br>Adaptive Reasoning Method</div>
    </div>

    <svg class="contact-band" viewBox="0 0 600 343" aria-hidden="true">
      <path d="M0 200 H540 Q592 200 600 246 V343 H0 Z" fill="var(--slate)"/>
      <path d="M0 206 H540 Q588 206 600 250 V343 H0 Z" fill="var(--teal)"/>
    </svg>

    <div class="person">
      <div class="person-name">MARA LINDQVIST</div>
      <div class="person-title">CEO/FOUNDER</div>
      <ul class="contact-list">
        <li>
          <svg viewBox="0 0 24 24"><path d="M6.6 10.8a15.1 15.1 0 0 0 6.6 6.6l2.2-2.2c.3-.3.7-.4 1-.2 1.1.4 2.3.6 3.6.6.6 0 1 .4 1 1V20c0 .6-.4 1-1 1A17 17 0 0 1 3 4c0-.6.4-1 1-1h3.5c.6 0 1 .4 1 1 0 1.3.2 2.5.6 3.6.1.3 0 .7-.2 1z"/></svg>
          555 210 4187
        </li>
        <li>
          <svg viewBox="0 0 24 24"><path d="M2 5h20v2l-10 6L2 7zM2 9.3l10 6 10-6V19H2z"/></svg>
          hello@kvormail.com
        </li>
      </ul>
    </div>

    <div class="company">
      <div class="company-name">Coherent Lattice Of<br>Adaptive Reasoning Method</div>
      <div class="company-address">4120 Alder Crest Way<br>Harbor Point, Alaska 99512</div>
    </div>
  </section>

  <section class="card card-back" aria-label="Business card back">
    <div class="brand">
      <div class="brand-name">KVOR<span class="brand-mark"></span></div>
      <div class="brand-full">Coherent Lattice of<br>Adaptive Reasoning Method</div>
    </div>
    <p class="tagline">Sharpening Clarity for Driven Teams and Their Leaders</p>
  </section>

</main>
</body>
</html>
```